Bicycle dealer and service & repair center

The registered brand of our company, Rad Lindhof, means bicycle of the city Zurich (Switzerland) and is the largest dealer of e-bikes, folding bikes and cargo bikes in Switzerland. Rad Lindhof also sells a substantial amount of road bikes, mountainbikes, trailers and bicycles without electric motor. The more, we are known for special bikes (tandems, Swiss military bicycles, postman bicycles, and others).Rad Lindhof has around 10 highly skilled employees and runs a well-equipped service & repair center. We have around 50 brand dealerships for replacement parts, diagnostic devices and are proud about our after-sales service.Our website is fully functional (see www.rad-lindhof.ch) and available in three languages (DE, EN, FR for the french speaking part of Switzerland). Live stock information is provided by https://www.rad-lindhof.ch/en/rad.We need a redesign of our website. The focus should be on:- e-catalog with simple search and extended search - e-commerce (e.g. add to chart, favorites, text search, filter, sort, related products, similar products, most popular search, related articles, top listings, promotions...)- cross-selling with our affiliated company Rad Brunnegg, our bicycle shop in a city nearby Zurich.- service and repair- company (sustainable business, emission-free mobility, public relation, well-trained and friendly staff)- mobile friendlyness- maximize usability- maximize usage of display for useful information- easy to find relevant information- simple search functionalityKey audience is:- middle to high-price bicycle customers- existing and returning clients- prospective employees- members of the pressThe goal of the website and its redesign is:- increase the number of enquiries via website- increase online sales- share information with others (addtoany)- provide information about the right selection of bicycle (faq, detailed information about components) to reduce the admin associated with new enquiries- highlight special offers (e.g. free bicycle service slots, sunday exhibition)As Rad Lindhof has many returning customers and already high website traffic (according to SERP), the new design should be a smooth transition from the existing website.Websites we like:- https://tramofix.ch/- https://www.kurbelhaus.ch/- https://www.quandor.ch/- https://www.autoscout24.ch/deGood luck and have fun creating our new design!
Updates

website we also like: https://www.pedalora.ch/

Target Market(s)

Urban bicycle riders

Industry/Entity Type

Retail

Coding

Coded - Design and coding required

Number of Pages Required

5+ page

Font styles to use
Other font styles liked:
• Avenir (https://www.glyphbazar.com/fonts/typecraft/avenir/)

Colors

Designer to choose colors to be used in the design.

Requirements
Must have
• The actual content www.rad-lindhof.ch must be published with the new website design. Additional content should be added according to project description (see above).
Nice to have
• - we use the font type Avenir (https://www.glyphbazar.com/fonts/typecraft/avenir/) for business cards, leaflets etc
Should not have
• Frippery

```html
<!DOCTYPE html>
<html lang="en">
<head>
<meta charset="utf-8">
<title>Rad Lindhof – E-Bikes, Cargobikes, Service</title>
<link href="https://fonts.googleapis.com/css2?family=Nunito+Sans:wght@400;600;700;800;900&family=Raleway:wght@500;600;700;800&display=swap" rel="stylesheet">
<style>
:root{
  --blue:#1d679e;
  --blue-dark:#175684;
  --ink:#222;
  --text:#444;
  --muted:#777;
  --line:#d6d6d6;
  --topbar:#222;
  --footer:#1f1f1f;
  --footer-text:#cfcfcf;
  --card-bg:#f1f1f1;
}
*{box-sizing:border-box;margin:0;padding:0}
html,body{width:1200px;height:4167px;overflow:hidden;background:#fff}
body{font-family:"Nunito Sans",Arial,sans-serif;color:var(--text);position:relative}
.abs{position:absolute}
.topbar{position:absolute;left:0;top:0;width:1200px;height:32px;background:var(--topbar);color:#ddd;font-size:14px}
.topbar .left{position:absolute;left:112px;top:7px;display:flex;gap:10px;align-items:center}
.topbar .right{position:absolute;right:112px;top:7px;display:flex;gap:10px;align-items:center}
.topbar svg{width:12px;height:12px;fill:#ddd;margin-right:5px;vertical-align:-1px}
.sep{color:#888}
.header{position:absolute;left:0;top:32px;width:1200px;height:93px;border-bottom:1px solid var(--line)}
.brand{position:absolute;left:112px;top:16px;display:flex;align-items:center;gap:10px}
.brand-name{font-family:"Raleway",sans-serif;font-weight:800;font-size:36px;color:var(--ink);letter-spacing:-.5px;line-height:1}
.brand-mark{width:62px;height:62px;background:var(--blue);border-radius:6px}
.brand-tag{position:absolute;left:112px;top:64px;font-size:9.5px;color:#333}
.search{position:absolute;left:651px;top:26px;width:358px;height:42px;border:1px solid #bbb;font-size:15px;color:#999;padding:11px 14px}
.search svg{position:absolute;right:10px;top:11px;width:18px;height:18px}
.cart{position:absolute;left:1038px;top:23px;width:50px;height:50px;border-radius:50%;background:var(--blue)}
.cart svg{position:absolute;left:14px;top:15px;width:22px;height:20px;fill:#fff}
.nav{position:absolute;left:0;top:125px;width:1200px;height:45px}
.nav a{font-size:15px;font-weight:600;color:#222;text-decoration:none;line-height:45px;position:absolute;top:0}
.nav a.active{color:var(--blue)}
.hero{position:absolute;left:0;top:170px;width:1200px;height:543px;background:linear-gradient(90deg,#9aa39a 0%,#dfe6da 20%,#b9c43c 38%,#8a8f6a 55%,#a8a08a 75%,#6f7a52 100%)}
.hero-photo{position:absolute;inset:0;background:linear-gradient(180deg,rgba(255,255,255,.15),rgba(0,0,0,.1) 60%,rgba(60,70,30,.35))}
.hero h1{position:absolute;left:698px;top:118px;font-family:"Raleway",sans-serif;font-weight:800;font-size:64px;color:#fff;letter-spacing:1px}
.hero p{position:absolute;left:701px;top:217px;width:410px;font-size:17.5px;line-height:32.5px;color:#fff}
.btn-ghost{position:absolute;left:702px;top:355px;width:163px;height:54px;border:2px solid #fff;border-radius:27px;color:#fff;font-weight:800;font-size:17px;text-align:center;line-height:50px}
.dots{position:absolute;left:566px;top:464px;display:flex;gap:4px}
.dots span{width:15px;height:15px;border-radius:50%;border:2px solid #fff}
.dots span.on{background:#fff}
.section-title{position:absolute;width:1200px;text-align:center;font-family:"Raleway",sans-serif;font-weight:700;font-size:34px;color:var(--ink)}
.filter-label{position:absolute;top:870px;font-size:15px;color:#333}
.select{position:absolute;height:41px;border:1px solid #bbb;font-size:14px;color:#999;padding:11px 12px;background:#fff}
.select .caret{position:absolute;right:0;top:0;width:40px;height:39px;border-left:1px solid #bbb}
.select .caret:after{content:"";position:absolute;left:15px;top:17px;border:5px solid transparent;border-top:6px solid #555}
.btn{position:absolute;background:var(--blue);color:#fff;font-weight:800;text-align:center;border-radius:28px}
.reset{position:absolute;right:128px;top:960px;font-size:15px;color:#333}
.reset svg{width:13px;height:13px;vertical-align:-1px;margin-right:5px}
.rule{position:absolute;left:112px;width:976px;height:2px;background:#cfcfcf}
.sortby{position:absolute;left:749px;top:1067px;font-size:15px;color:#333}
.view-icons{position:absolute;left:1034px;top:1071px;display:flex;gap:17px}
.card{position:absolute;width:233px;height:318px;border:1px solid #ccc;background:#fff}
.card .img{height:212px;background:var(--card-bg);position:relative}
.card .heart{position:absolute;right:10px;bottom:8px;width:20px;height:18px}
.card .price{position:absolute;left:18px;top:228px;color:var(--blue);font-weight:800;font-size:16px}
.card .name{position:absolute;left:18px;top:252px;font-size:18.5px;font-weight:600;color:#222}
.card .type{position:absolute;left:18px;top:283px;font-size:14.5px;color:#666}
.promo{position:absolute;left:112px;top:2705px;width:976px;height:408px;background:linear-gradient(180deg,#8d8f8c 0%,#6e6f6d 30%,#4a4d52 65%,#33363b 100%)}
.promo .sub{position:absolute;width:976px;top:70px;text-align:center;color:#fff;font-family:"Raleway",sans-serif;font-weight:600;font-size:37px}
.promo .big{position:absolute;width:976px;top:122px;text-align:center;color:#fff;font-family:"Raleway",sans-serif;font-weight:800;font-size:54px}
.article{position:absolute;top:3294px;width:311px;height:325px;border:1px solid #ccc;background:#fff}
.article .img{height:231px}
.article h3{position:absolute;width:100%;top:248px;text-align:center;font-size:20px;font-weight:600;color:#222}
.article .meta{position:absolute;width:100%;top:285px;text-align:center;font-size:14px;color:#555}
.article .meta svg{width:12px;height:12px;fill:#d9a21f;vertical-align:-1px;margin-right:5px}
.article .meta .u{fill:var(--blue)}
.arrow{position:absolute;top:3432px;width:46px;height:46px;border-radius:50%;border:1px solid #999;background:#fff}
.arrow svg{position:absolute;left:14px;top:13px;width:18px;height:18px}
.footer{position:absolute;left:0;top:3719px;width:1200px;height:448px;background:var(--footer);color:var(--footer-text)}
.footer h4{position:absolute;top:63px;font-size:19px;font-weight:700;color:#fff}
.footer ul{position:absolute;top:105px;list-style:none;font-size:14px;line-height:31.5px}
.contact-line{position:absolute;left:108px;font-size:14px;line-height:18px;display:flex;gap:12px}
.contact-line svg{width:13px;height:13px;fill:#fff;flex:none;margin-top:2px}
.newsletter p{position:absolute;left:786px;top:102px;width:310px;font-size:14px;line-height:27px}
.nl-input{position:absolute;left:789px;top:178px;width:224px;height:42px;background:#fff;color:#555;font-size:14px;padding:12px 18px}
.nl-btn{position:absolute;left:1013px;top:178px;width:75px;height:42px;background:var(--blue);color:#fff;font-weight:800;font-size:14px;text-align:center;line-height:42px}
.social{position:absolute;top:240px;width:44px;height:44px;border-radius:50%;border:1.5px solid #bbb}
.pay{position:absolute;top:386px;width:40px;height:25px;border-radius:3px;background:#5a5a5a}
</style>
</head>
<body>

<div class="topbar">
  <div class="left">
    <span><svg viewBox="0 0 24 24"><path d="M6.6 10.8a15 15 0 0 0 6.6 6.6l2.2-2.2c.3-.3.7-.4 1-.2 1.1.4 2.3.6 3.6.6.6 0 1 .4 1 1V20c0 .6-.4 1-1 1A17 17 0 0 1 3 4c0-.6.4-1 1-1h3.5c.6 0 1 .4 1 1 0 1.3.2 2.5.6 3.6.1.3 0 .7-.2 1z"/></svg>+41 (0) 44 870 35 12</span>
    <span class="sep">|</span>
    <span><svg viewBox="0 0 24 24"><path d="M2 5h20v14H2zm2 2v.5l8 6 8-6V7z"/></svg>info@rad-lindhof.ch</span>
  </div>
  <div class="right">
    <span><svg viewBox="0 0 24 24"><path d="M12 21 3 12a5 5 0 0 1 9-6 5 5 0 0 1 9 6z"/></svg>Favorites</span>
    <span class="sep">|</span>
    <span><svg viewBox="0 0 24 24"><path d="M6 10V7a6 6 0 0 1 12 0v3h2v12H4V10zm3 0h6V7a3 3 0 0 0-6 0z"/></svg>Login</span>
    <span class="sep">|</span>
    <span>Eng ▾</span>
  </div>
</div>

<header class="header">
  <div class="brand"><span class="brand-name">RAD LINDHOF</span><span class="brand-mark"></span></div>
  <div class="brand-tag">E-Bikes | Cargobikes | Velos | Service &amp; Reparaturen</div>
  <div class="search">Search
    <svg viewBox="0 0 24 24" fill="none" stroke="#555" stroke-width="2.5"><circle cx="10" cy="10" r="7"/><path d="m15 15 6 6"/></svg>
  </div>
  <div class="cart"><svg viewBox="0 0 24 22"><path d="M0 1h4l1 3h19l-3 9H7.5l.7 2H21v2H6.8L3 3H0z"/><circle cx="9" cy="20" r="2"/><circle cx="19" cy="20" r="2"/></svg></div>
</header>

<nav class="nav">
  <a class="active" style="left:145px">HOME</a>
  <a style="left:259px">ABOUT</a>
  <a style="left:377px">VELOS</a>
  <a style="left:492px">NEWS</a>
  <a style="left:603px">SERVICES</a>
  <a style="left:740px">ABOUT US</a>
  <a style="left:883px">FAQ</a>
  <a style="left:980px">CONTACT</a>
</nav>

<section class="hero">
  <div class="hero-photo" role="img" aria-label="White e-bike parked beside a lime green wall in a sunny field"></div>
  <h1>E-BIKES</h1>
  <p>With over 300 different e-bikes, Rad Lindhof GmbH offers the largest selection of pedelecs and s-pedelecs in Switzerland.</p>
  <div class="btn-ghost">SHOP NOW!</div>
  <div class="dots"><span class="on"></span><span></span><span></span><span></span></div>
</section>

<h2 class="section-title" style="top:785px">ALL BIKES IN SWITZERLAND</h2>

<span class="filter-label" style="left:110px">Year:</span>
<span class="filter-label" style="left:320px">Brand:</span>
<span class="filter-label" style="left:530px">Model:</span>
<span class="filter-label" style="left:739px">Price:</span>
<div class="select" style="left:112px;top:902px;width:185px">All<span class="caret"></span></div>
<div class="select" style="left:320px;top:902px;width:185px">All<span class="caret"></span></div>
<div class="select" style="left:530px;top:902px;width:185px">All<span class="caret"></span></div>
<div class="select" style="left:739px;top:902px;width:186px">All<span class="caret"></span></div>
<div class="btn" style="left:954px;top:894px;width:134px;height:54px;line-height:54px;font-size:18px">SEARCH</div>
<div class="reset"><svg viewBox="0 0 24 24" fill="none" stroke="#333" stroke-width="3"><path d="M20 12a8 8 0 1 1-3-6.2"/><path d="M18 2v5h-5" /></svg>Reset Filter</div>
<div class="rule" style="top:1006px"></div>

<span class="sortby">Sort By</span>
<div class="select" style="left:818px;top:1061px;width:185px;height:37px;padding:9px 14px">Top listings<span class="caret" style="height:35px"></span></div>
<div class="view-icons">
  <svg width="19" height="15" viewBox="0 0 19 15" fill="#1d679e"><rect width="5" height="4"/><rect x="7" width="5" height="4"/><rect x="14" width="5" height="4"/><rect y="5.5" width="5" height="4"/><rect x="7" y="5.5" width="5" height="4"/><rect x="14" y="5.5" width="5" height="4"/><rect y="11" width="5" height="4"/><rect x="7" y="11" width="5" height="4"/><rect x="14" y="11" width="5" height="4"/></svg>
  <svg width="19" height="15" viewBox="0 0 19 15" fill="#888"><rect width="4" height="3"/><rect x="6" width="13" height="3"/><rect y="6" width="4" height="3"/><rect x="6" y="6" width="13" height="3"/><rect y="12" width="4" height="3"/><rect x="6" y="12" width="13" height="3"/></svg>
</div>

<div class="card" style="left:112px;top:1150px"><div class="img" role="img" aria-label="Black racing bike"><svg class="heart" viewBox="0 0 24 22" fill="none" stroke="#1d679e" stroke-width="2"><path d="M12 20 3 11a5 5 0 0 1 9-6 5 5 0 0 1 9 6z"/></svg></div><div class="price">CHF 1'859.-</div><div class="name">Pathline ALR 4</div><div class="type">Racing bike</div></div>
<div class="card" style="left:359px;top:1150px"><div class="img" role="img" aria-label="Dark blue e-bike"><svg class="heart" viewBox="0 0 24 22" fill="none" stroke="#1d679e" stroke-width="2"><path d="M12 20 3 11a5 5 0 0 1 9-6 5 5 0 0 1 9 6z"/></svg></div><div class="price">CHF 1'859.-</div><div class="name">Pathline ALR 4</div><div class="type">Racing bike</div></div>
<div class="card" style="left:606px;top:1150px"><div class="img" role="img" aria-label="Lime green folding bike"><svg class="heart" viewBox="0 0 24 22" fill="none" stroke="#1d679e" stroke-width="2"><path d="M12 20 3 11a5 5 0 0 1 9-6 5 5 0 0 1 9 6z"/></svg></div><div class="price">CHF 1'859.-</div><div class="name">Pathline ALR 4</div><div class="type">Racing bike</div></div>
<div class="card" style="left:855px;top:1150px"><div class="img" role="img" aria-label="Olive green e-bike"><svg class="heart" viewBox="0 0 24 22" fill="none" stroke="#1d679e" stroke-width="2"><path d="M12 20 3 11a5 5 0 0 1 9-6 5 5 0 0 1 9 6z"/></svg></div><div class="price">CHF 1'859.-</div><div class="name">Pathline ALR 4</div><div class="type">Racing bike</div></div>

<div class="card" style="left:112px;top:1489px"><div class="img" role="img" aria-label="Black electric folding bike"><svg class="heart" viewBox="0 0 24 22" fill="none" stroke="#1d679e" stroke-width="2"><path d="M12 20 3 11a5 5 0 0 1 9-6 5 5 0 0 1 9 6z"/></svg></div><div class="price">CHF 1'859.-</div><div class="name">Pathline ALR 4</div><div class="type">Racing bike</div></div>
<div class="card" style="left:359px;top:1489px"><div class="img" role="img" aria-label="Black trekking e-bike"><svg class="heart" viewBox="0 0 24 22" fill="none" stroke="#1d679e" stroke-width="2"><path d="M12 20 3 11a5 5 0 0 1 9-6 5 5 0 0 1 9 6z"/></svg></div><div class="price">CHF 1'859.-</div><div class="name">Pathline ALR 4</div><div class="type">Racing bike</div></div>
<div class="card" style="left:606px;top:1489px"><div class="img" role="img" aria-label="Brown city e-bike"><svg class="heart" viewBox="0 0 24 22" fill="none" stroke="#1d679e" stroke-width="2"><path d="M12 20 3 11a5 5 0 0 1 9-6 5 5 0 0 1 9 6z"/></svg></div><div class="price">CHF 1'859.-</div><div class="name">Pathline ALR 4</div><div class="type">Racing bike</div></div>
<div class="card" style="left:855px;top:1489px"><div class="img" role="img" aria-label="Light blue step-through e-bike"><svg class="heart" viewBox="0 0 24 22" fill="none" stroke="#1d679e" stroke-width="2"><path d="M12 20 3 11a5 5 0 0 1 9-6 5 5 0 0 1 9 6z"/></svg></div><div class="price">CHF 1'859.-</div><div class="name">Pathline ALR 4</div><div class="type">Racing bike</div></div>

<div class="card" style="left:112px;top:1827px"><div class="img" role="img" aria-label="Green cargo bike"><svg class="heart" viewBox="0 0 24 22" fill="none" stroke="#1d679e" stroke-width="2"><path d="M12 20 3 11a5 5 0 0 1 9-6 5 5 0 0 1 9 6z"/></svg></div><div class="price">CHF 1'859.-</div><div class="name">Pathline ALR 4</div><div class="type">Racing bike</div></div>
<div class="card" style="left:359px;top:1827px"><div class="img" role="img" aria-label="Red and black folding bike"><svg class="heart" viewBox="0 0 24 22" fill="none" stroke="#1d679e" stroke-width="2"><path d="M12 20 3 11a5 5 0 0 1 9-6 5 5 0 0 1 9 6z"/></svg></div><div class="price">CHF 1'859.-</div><div class="name">Pathline ALR 4</div><div class="type">Racing bike</div></div>
<div class="card" style="left:606px;top:1827px"><div class="img" role="img" aria-label="Grey step-through e-bike"><svg class="heart" viewBox="0 0 24 22" fill="none" stroke="#1d679e" stroke-width="2"><path d="M12 20 3 11a5 5 0 0 1 9-6 5 5 0 0 1 9 6z"/></svg></div><div class="price">CHF 1'859.-</div><div class="name">Pathline ALR 4</div><div class="type">Racing bike</div></div>
<div class="card" style="left:855px;top:1827px"><div class="img" role="img" aria-label="Compact folding bike with spec sheet"><svg class="heart" viewBox="0 0 24 22" fill="none" stroke="#1d679e" stroke-width="2"><path d="M12 20 3 11a5 5 0 0 1 9-6 5 5 0 0 1 9 6z"/></svg></div><div class="price">CHF 1'859.-</div><div class="name">Pathline ALR 4</div><div class="type">Racing bike</div></div>

<div class="card" style="left:112px;top:2167px"><div class="img" role="img" aria-label="Red sporty e-bike"><svg class="heart" viewBox="0 0 24 22" fill="none" stroke="#1d679e" stroke-width="2"><path d="M12 20 3 11a5 5 0 0 1 9-6 5 5 0 0 1 9 6z"/></svg></div><div class="price">CHF 1'859.-</div><div class="name">Pathline ALR 4</div><div class="type">Racing bike</div></div>
<div class="card" style="left:359px;top:2167px"><div class="img" role="img" aria-label="Cream city e-bike"><svg class="heart" viewBox="0 0 24 22" fill="none" stroke="#1d679e" stroke-width="2"><path d="M12 20 3 11a5 5 0 0 1 9-6 5 5 0 0 1 9 6z"/></svg></div><div class="price">CHF 1'859.-</div><div class="name">Pathline ALR 4</div><div class="type">Racing bike</div></div>
<div class="card" style="left:606px;top:2167px"><div class="img" role="img" aria-label="White trekking e-bike"><svg class="heart" viewBox="0 0 24 22" fill="none" stroke="#1d679e" stroke-width="2"><path d="M12 20 3 11a5 5 0 0 1 9-6 5 5 0 0 1 9 6z"/></svg></div><div class="price">CHF 1'859.-</div><div class="name">Pathline ALR 4</div><div class="type">Racing bike</div></div>
<div class="card" style="left:855px;top:2167px"><div class="img" role="img" aria-label="Black and blue mountain e-bike"><svg class="heart" viewBox="0 0 24 22" fill="none" stroke="#1d679e" stroke-width="2"><path d="M12 20 3 11a5 5 0 0 1 9-6 5 5 0 0 1 9 6z"/></svg></div><div class="price">CHF 1'859.-</div><div class="name">Pathline ALR 4</div><div class="type">Racing bike</div></div>

<div class="btn" style="left:517px;top:2553px;width:165px;height:55px;line-height:55px;font-size:17px">VIEW MORE</div>

<section class="promo" role="img" aria-label="Showroom with rows of e-bikes under a concrete ceiling">
  <div class="sub">SAVE UP TO 30%</div>
  <div class="big">UBER 400 E-BIKES AN LARGER!</div>
  <div class="btn" style="left:402px;top:215px;width:173px;height:52px;line-height:52px;font-size:17px">SHOP NOW!</div>
</section>

<h2 class="section-title" style="top:3203px">RELATED ARTICLES</h2>

<div class="arrow" style="left:31px"><svg viewBox="0 0 24 24" fill="none" stroke="#444" stroke-width="2.5"><path d="M15 4 7 12l8 8"/></svg></div>
<div class="arrow" style="left:1122px"><svg viewBox="0 0 24 24" fill="none" stroke="#444" stroke-width="2.5"><path d="m9 4 8 8-8 8"/></svg></div>

<article class="article" style="left:112px"><div class="img" role="img" aria-label="Mechanic repairing a bicycle wheel in the workshop" style="background:linear-gradient(135deg,#d9dde2,#8c949c 60%,#3d4852)"></div><h3>Velo-mechanics wanted</h3><div class="meta"><svg viewBox="0 0 24 24"><path d="M3 5h18v16H3zM7 2v5M17 2v5"/></svg>09/05/2019 &nbsp;|&nbsp; <svg class="u" viewBox="0 0 24 24"><circle cx="12" cy="7" r="5"/><path d="M3 22a9 9 0 0 1 18 0z"/></svg>Lena Marti</div></article>
<article class="article" style="left:445px"><div class="img" role="img" aria-label="Rows of discounted bikes with sale tags" style="background:linear-gradient(135deg,#cdd4d8,#3ab0d6 55%,#2b2e33)"></div><h3>Sale of old models</h3><div class="meta"><svg viewBox="0 0 24 24"><path d="M3 5h18v16H3zM7 2v5M17 2v5"/></svg>05/02/2019 &nbsp;|&nbsp; <svg class="u" viewBox="0 0 24 24"><circle cx="12" cy="7" r="5"/><path d="M3 22a9 9 0 0 1 18 0z"/></svg>Lena Marti</div></article>
<article class="article" style="left:776px"><div class="img" role="img" aria-label="Video still of a shop owner interview" style="background:linear-gradient(135deg,#6a5a4e,#a5806a 50%,#2a2625)"></div><h3>Rad Lindhof in the news</h3><div class="meta"><svg viewBox="0 0 24 24"><path d="M3 5h18v16H3zM7 2v5M17 2v5"/></svg>04/16/2019 &nbsp;|&nbsp; <svg class="u" viewBox="0 0 24 24"><circle cx="12" cy="7" r="5"/><path d="M3 22a9 9 0 0 1 18 0z"/></svg>Lena Marti</div></article>

<footer class="footer">
  <h4 style="left:108px">Contact Us</h4>
  <div class="contact-line" style="top:113px"><svg viewBox="0 0 24 24"><path d="M12 2a7 7 0 0 0-7 7c0 5 7 13 7 13s7-8 7-13a7 7 0 0 0-7-7zm0 9.5A2.5 2.5 0 1 1 12 6.5a2.5 2.5 0 0 1 0 5z"/></svg><span>Lindhofweg 18<br>CH-8048 Zurich</span></div>
  <div class="contact-line" style="top:167px"><svg viewBox="0 0 24 24"><path d="M6.6 10.8a15 15 0 0 0 6.6 6.6l2.2-2.2c.3-.3.7-.4 1-.2 1.1.4 2.3.6 3.6.6.6 0 1 .4 1 1V20c0 .6-.4 1-1 1A17 17 0 0 1 3 4c0-.6.4-1 1-1h3.5c.6 0 1 .4 1 1 0 1.3.2 2.5.6 3.6.1.3 0 .7-.2 1z"/></svg><span>+41 (0) 44 870 35 12</span></div>
  <div class="contact-line" style="top:205px"><svg viewBox="0 0 24 24"><path d="M2 5h20v14H2zm2 2v.5l8 6 8-6V7z"/></svg><span>info@rad-lindhof.ch</span></div>
  <div class="contact-line" style="top:245px;width:170px;font-size:13.5px"><span>VAT CHE-248.519.306<br>Trade Register : CH-020.4.118.562-3</span></div>

  <h4 style="left:332px">Quick Links</h4>
  <ul style="left:332px"><li>Advanced Search</li><li>Search garages &amp; dealers</li><li>Brand Overview</li><li>Advertise</li><li>Products and prices</li></ul>

  <h4 style="left:555px">Shop with Confidence</h4>
  <ul style="left:555px"><li>Our 100% Guarantee</li><li>Product Warranty</li><li>Privacy &amp; Security</li><li>Terms &amp; Conditions</li><li>How To Order</li></ul>

  <h4 style="left:786px">Sign up for our newsletter</h4>
  <div class="newsletter"><p>Get the latest updates on new products and upcoming sales</p></div>
  <div class="nl-input">Email Address</div>
  <div class="nl-btn">SIGN UP!</div>
  <span class="social" style="left:786px" aria-label="Social link 1"></span>
  <span class="social" style="left:842px" aria-label="Social link 2"></span>
  <span class="social" style="left:897px" aria-label="Social link 3"></span>
  <span class="social" style="left:953px" aria-label="Social link 4"></span>

  <div class="rule" style="top:344px;height:1px;background:#444"></div>
  <div class="abs" style="left:114px;top:388px;font-size:14px">© 2019, Rad-lindhof. All rights reserved.</div>

  <span class="pay" style="left:857px" aria-label="Payment card"></span>
  <span class="pay" style="left:905px" aria-label="Payment card"></span>
  <span class="pay" style="left:953px" aria-label="Payment card"></span>
  <span class="pay" style="left:1000px" aria-label="Payment card"></span>
  <span class="pay" style="left:1048px" aria-label="Payment card"></span>
</footer>

</body>
</html>
```